I have a logo and need to design the business card and stationery.
Updates

The uploaded logo image named as GREYMARSH CONSTRUCTION which is to be replaced to GREYMARSH CONTRACTS. Kindly add below details and submit the designs- Company name- Greymarsh Engineering Contracts LLP Name & Post- Kelvan Joshi (Designated Partner) Address- Block No.317, Wing C, Tulvo Trade Court, Manek Pural Road, Ruparel Industrial Estate, Goregaon(E), Mumbai - 400 063 Contact- +91 97415 60382 Email- kelvanjoshi@mailbrook.example Website- www.greymarshcontracts.example Contact for Letterhead- +91-22-28754193

Hi Tovin Rahul, We are liking your Design #28860835. We have suggested some changes which are mentioned in feedback. Kindly revert with it asap to finalize this design.

Colors

Designer to choose colors to be used in the design.

```html
<!DOCTYPE html>
<html lang="en">
<head>
<meta charset="utf-8">
<title>Greymarsh Contracts – Business Card</title>
<link rel="stylesheet" href="https://fonts.googleapis.com/css2?family=Poppins:wght@400;600&display=swap">
<style>
  :root {
    --backdrop: #cfcccb;
    --card-dark: #1c1c1c;
    --card-dark-panel: #151515;
    --mark-dark: #4a4a4a;
    --card-light: #f3f3f3;
    --mark-light: #e2e3e3;
    --ink: #1a1a1a;
    --ink-soft: #3a3a3a;
    --paper-white: #ffffff;
    --muted-grey: #8a8a8a;
  }
  * { box-sizing: border-box; margin: 0; padding: 0; }
  html, body { width: 1200px; height: 1014px; overflow: hidden; }
  body {
    background: var(--backdrop);
    font-family: "Poppins", sans-serif;
    position: relative;
  }
  .card {
    position: absolute;
    left: 280px;
    width: 640px;
    height: 352px;
    overflow: hidden;
    box-shadow: 0 6px 18px rgba(0,0,0,0.25);
  }
  .card--front { top: 143px; background: var(--card-dark); }
  .card--back  { top: 519px; background: var(--card-light); }

  /* front */
  .front-panel {
    position: absolute; left: 333px; top: 0; right: 0; bottom: 0;
    background: var(--card-dark-panel);
  }
  .front-mark {
    position: absolute; left: 392px; top: 18px;
    width: 230px; height: 214px;
    background: var(--mark-dark);
  }
  .wordmark {
    font-weight: 600;
    text-transform: uppercase;
    line-height: 1.05;
    letter-spacing: 0.04em;
  }
  .wordmark span { display: block; }
  .front-wordmark {
    position: absolute; left: 56px; top: 246px;
    color: var(--paper-white);
    font-size: 21px;
  }
  .front-website {
    position: absolute; left: 366px; top: 264px;
    color: var(--paper-white);
    font-size: 14px;
  }

  /* back */
  .back-mark {
    position: absolute; left: 348px; top: 0;
    width: 292px; height: 272px;
    background: var(--mark-light);
  }
  .back-logo {
    position: absolute; left: 48px; top: 44px;
    display: flex; flex-direction: column; align-items: center; gap: 10px;
  }
  .logo-square {
    width: 56px; height: 56px;
    background: var(--ink);
  }
  .back-wordmark {
    color: var(--ink);
    font-size: 17px;
    text-align: center;
  }
  .contact-name {
    position: absolute; left: 52px; top: 178px;
    color: var(--ink);
    font-size: 22px;
    font-weight: 400;
    line-height: 1.1;
  }
  .contact-name strong { font-weight: 600; }
  .contact-role {
    position: absolute; left: 52px; top: 205px;
    color: var(--ink-soft);
    font-size: 13px;
  }
  .contact-list {
    position: absolute; left: 48px; top: 236px;
    list-style: none;
    color: var(--ink-soft);
    font-size: 14px;
  }
  .contact-list li { display: flex; align-items: center; gap: 8px; height: 23px; }
  .contact-list svg { width: 13px; height: 13px; flex: none; }
  .address {
    position: absolute; left: 48px; top: 296px;
    color: var(--ink-soft);
    font-size: 12px;
    line-height: 1.45;
  }
</style>
</head>
<body>
  <section class="card card--front" aria-label="Business card front">
    <div class="front-panel"></div>
    <div class="front-mark"></div>
    <div class="wordmark front-wordmark"><span>Greymarsh</span><span>Contracts</span></div>
    <p class="front-website">www.greymarshcontracts.example</p>
  </section>

  <section class="card card--back" aria-label="Business card back">
    <div class="back-mark"></div>
    <div class="back-logo">
      <div class="logo-square"></div>
      <div class="wordmark back-wordmark"><span>Greymarsh</span><span>Contracts</span></div>
    </div>
    <h1 class="contact-name"><strong>Kelvan</strong> Joshi</h1>
    <p class="contact-role">(Designated Partner)</p>
    <ul class="contact-list">
      <li>
        <svg viewBox="0 0 16 16" aria-hidden="true"><circle cx="8" cy="8" r="8" fill="var(--ink)"/><path d="M5.2 4.2l1.5-.3.8 1.9-1 .8c.5 1.1 1.3 1.9 2.4 2.4l.8-1 1.9.8-.3 1.5c-3.4.2-6.3-2.7-6.1-6.1z" fill="#fff"/></svg>
        +91 97415 60382
      </li>
      <li>
        <svg viewBox="0 0 16 16" aria-hidden="true"><circle cx="8" cy="8" r="8" fill="var(--ink)"/><rect x="4" y="5" width="8" height="6" fill="#fff"/><path d="M4 5l4 3.2L12 5" fill="none" stroke="var(--ink)" stroke-width="1"/></svg>
        kelvanjoshi@mailbrook.example
      </li>
    </ul>
    <p class="address">Block No.317, Wing C, Tulvo Trade Court, Manek Pural Road,<br>Ruparel Industrial Estate, Goregaon(E), Mumbai - 400 063</p>
  </section>
</body>
</html>
```